Software allocation system needs a business card design

We need a business card designed for our software platform - www.tallivo.com.au

At the moment the logo and website is all black and white, we are happy for suggestions on implementing some colour throughout either the logo or business card.

Industry/Entity Type

Software

Font styles to use
Sans Serif

Colors

Designer to choose colors to be used in the design.

```html
<!DOCTYPE html>
<html lang="en">
<head>
<meta charset="utf-8">
<title>Tallivo – Business Card</title>
<link rel="stylesheet" href="https://fonts.googleapis.com/css2?family=Arimo:wght@400;500&display=swap">
<style>
  :root {
    --ink: #1b2036;
    --ink-soft: #2f3240;
    --paper: #ffffff;
    --paper-shade: #eef0f3;
    --accent-bar: #1b2036;
  }
  * { box-sizing: border-box; margin: 0; padding: 0; }
  html, body {
    width: 1200px;
    height: 636px;
    overflow: hidden;
    background: var(--paper);
  }
  .card {
    position: relative;
    width: 1200px;
    height: 636px;
    overflow: hidden;
    font-family: "Arimo", Arial, sans-serif;
    color: var(--ink);
    background: linear-gradient(125deg, var(--paper) 0%, var(--paper) 45%, var(--paper-shade) 100%);
  }
  .brand {
    position: absolute;
    left: 0;
    right: 0;
    top: 22px;
    text-align: center;
  }
  .brand-name {
    display: block;
    font-size: 178px;
    font-weight: 400;
    line-height: 1;
    letter-spacing: 10px;
    color: var(--ink);
  }
  .brand-tagline {
    display: block;
    margin-top: 6px;
    font-size: 26px;
    font-weight: 400;
    letter-spacing: 0.5px;
    color: var(--ink-soft);
  }
  .person {
    position: absolute;
    left: 124px;
    top: 388px;
  }
  .person-name {
    font-size: 70px;
    font-weight: 500;
    line-height: 1;
    color: var(--ink);
  }
  .person-role {
    margin-left: 54px;
    margin-top: -4px;
    font-size: 40px;
    font-weight: 400;
    line-height: 1;
    color: var(--ink-soft);
  }
  .contact {
    position: absolute;
    right: 40px;
    top: 352px;
    list-style: none;
    font-size: 27px;
    line-height: 1.2;
    color: var(--ink-soft);
  }
  .contact-item {
    display: flex;
    align-items: center;
    justify-content: flex-end;
    gap: 20px;
  }
  .contact-item + .contact-item { margin-top: 28px; }
  .contact-item.address { margin-top: 0; }
  .contact-text { text-align: right; }
  .contact-icon {
    width: 34px;
    height: 34px;
    flex: none;
    fill: var(--ink);
  }
  .accent-bar {
    position: absolute;
    right: 0;
    top: 343px;
    width: 8px;
    height: 293px;
    background: var(--accent-bar);
  }
</style>
</head>
<body>
  <main class="card">
    <header class="brand">
      <span class="brand-name">TALLIVO</span>
      <span class="brand-tagline">PLANNING &amp; COMPLIANCE FOR HEAVY INDUSTRY</span>
    </header>

    <section class="person">
      <h1 class="person-name">Jhon Smith</h1>
      <p class="person-role">Head Director</p>
    </section>

    <ul class="contact">
      <li class="contact-item address">
        <span class="contact-text">PO Box 218<br>Hollis Cove NSW 1580</span>
        <svg class="contact-icon" viewBox="0 0 24 24" aria-hidden="true">
          <path d="M12 2a7 7 0 0 0-7 7c0 5 7 13 7 13s7-8 7-13a7 7 0 0 0-7-7zm0 9.5A2.5 2.5 0 1 1 12 6.5a2.5 2.5 0 0 1 0 5z"/>
        </svg>
      </li>
      <li class="contact-item phone">
        <span class="contact-text">(insert phone number)</span>
        <svg class="contact-icon" viewBox="0 0 24 24" aria-hidden="true">
          <path d="M2 9c0-2 4-3.5 10-3.5S22 7 22 9v1.5h-4.5V9c-1.5-.6-3.5-.9-5.5-.9s-4 .3-5.5.9v1.5H2z"/>
          <path d="M6 11.5h12l2 7H4z"/>
        </svg>
      </li>
      <li class="contact-item email">
        <span class="contact-text">hello@tallivo.com.au</span>
        <svg class="contact-icon" viewBox="0 0 24 24" aria-hidden="true">
          <path d="M12 3a9 9 0 1 0 4.6 16.7l-.9-1.6A7.2 7.2 0 1 1 19.2 12v1c0 1-.6 1.7-1.4 1.7s-1.3-.7-1.3-1.7V8h-1.8v.8A4.5 4.5 0 1 0 15.1 15a3 3 0 0 0 2.7 1.5c1.9 0 3.2-1.5 3.2-3.5v-1a9 9 0 0 0-9-9zm0 11.8A2.8 2.8 0 1 1 12 9.2a2.8 2.8 0 0 1 0 5.6z"/>
        </svg>
      </li>
      <li class="contact-item web">
        <span class="contact-text">www.tallivo.com.au</span>
        <svg class="contact-icon" viewBox="0 0 24 24" aria-hidden="true">
          <circle cx="12" cy="13" r="5"/>
        </svg>
      </li>
    </ul>

    <div class="accent-bar"></div>
  </main>
</body>
</html>
```